Business card design for holistic health care clinic

We need a double-sided business card design for our holistic health care clinic that integrates our logo design and also its color scheme. My business is called Valmira. It is an integrative medicine clinic. You have already done the logo for me. Please ensure an elegant and upscale design that is not cluttered, but still has all the necessary information (please see below for details).

Target Market(s)

Wellness, fitness, rehabilitation for educated, well-traveled open-minded clients who are focused on natural, organic, balanced and preventive healthcare and lifestyle.

Industry/Entity Type

Medical

Contact Information for Business Card

Modern, clean.

Number of Pages Required

1 page

Font styles to use
Serif
Sans Serif

Colors

Designer to choose colors to be used in the design.

Requirements
Must have
• Logo on one side, all other information on the other side.
• Other information should include:
• Tobias Wrenfeld - DOE, CPT, LMT
• 4100 East Marrow Drive
• Austin, TX 78119
• 512 555 0148
• 818 555 0192
• info@ValmiraHealth.example
• t.wrenfeld@ValmiraHealth.example
Nice to have
• Darker background on front - but not totally black - shaded/dark gray.

```html
<!DOCTYPE html>
<html lang="en">
<head>
<meta charset="utf-8">
<title>Valmira business cards</title>
<link rel="stylesheet" href="https://fonts.googleapis.com/css2?family=Nunito:wght@600;700;800&family=Quicksand:wght@500&display=swap">
<style>
  :root {
    --brand-blue: #1a8fd1;
    --stage: #2a2a2a;
    --card-grey: #a7a7a7;
    --card-white: #f3f3f3;
    --ink: #3a3a3a;
    --ink-light: #ffffff;
  }
  * { margin: 0; padding: 0; box-sizing: border-box; }
  html, body { width: 1200px; height: 961px; overflow: hidden; }
  body { background: var(--stage); position: relative; font-family: "Quicksand", sans-serif; }

  .card {
    position: absolute;
    width: 453px;
    height: 258px;
    box-shadow: 0 3px 8px rgba(0,0,0,0.45);
  }
  .card--grey { background: var(--card-grey); }
  .card--white { background: var(--card-white); }
  .card--front-grey { left: 133px; top: 206px; }
  .card--front-white { left: 617px; top: 206px; }
  .card--back-white { left: 132px; top: 496px; }
  .card--back-grey { left: 615px; top: 496px; }

  .brand-name {
    font-family: "Nunito", sans-serif;
    font-weight: 800;
    color: var(--brand-blue);
    letter-spacing: 0.5px;
    text-transform: uppercase;
    line-height: 1;
  }
  .brand-tagline {
    font-family: "Nunito", sans-serif;
    font-weight: 700;
    color: var(--brand-blue);
    line-height: 1;
  }

  /* Contact side */
  .front .brand-name { position: absolute; left: 26px; top: 54px; font-size: 36px; }
  .front .brand-tagline { position: absolute; left: 29px; top: 91px; font-size: 11px; }

  .contact { position: absolute; left: 29px; top: 144px; font-size: 10.5px; color: var(--ink); line-height: 13px; }
  .contact__address { margin-bottom: 6px; }
  .contact__row { display: flex; align-items: center; gap: 6px; height: 14.5px; }
  .contact__icon { width: 10px; height: 10px; flex: none; }

  .practitioner { position: absolute; right: 32px; top: 171px; text-align: right; }
  .practitioner__name { font-family: "Nunito", sans-serif; font-weight: 800; font-size: 16px; color: var(--brand-blue); text-transform: uppercase; line-height: 1; }
  .practitioner__credentials { font-family: "Nunito", sans-serif; font-weight: 800; font-size: 9px; color: var(--brand-blue); margin-top: 3px; letter-spacing: 0.4px; }

  /* Logo side */
  .back { text-align: center; }
  .back .brand-name { position: absolute; left: 0; right: 0; top: 116px; font-size: 50px; }
  .back .brand-tagline { position: absolute; left: 0; right: 0; top: 170px; font-size: 16px; }
  .slogan {
    position: absolute; left: 0; right: 0; top: 211px;
    display: flex; justify-content: center; align-items: center;
    font-size: 13px; font-family: "Nunito", sans-serif; font-weight: 600;
  }
  .slogan::before, .slogan::after { content: ""; width: 48px; height: 1px; background: currentColor; opacity: 0.8; }
  .card--white .slogan { color: var(--brand-blue); }
  .card--grey .slogan { color: var(--ink-light); }
</style>
</head>
<body>

<svg width="0" height="0" style="position:absolute">
  <defs>
    <symbol id="icon-phone" viewBox="0 0 10 10"><path d="M2 0.5 L3.6 2.6 L2.7 3.6 Q3.6 5.6 6.3 7.3 L7.4 6.4 L9.5 8 L8.3 9.5 Q3.5 9 0.5 1.7 Z" fill="#1a8fd1"/></symbol>
    <symbol id="icon-mobile" viewBox="0 0 10 10"><rect x="2.5" y="0.5" width="5" height="9" rx="0.8" fill="none" stroke="#1a8fd1" stroke-width="1.2"/><circle cx="5" cy="8" r="0.6" fill="#1a8fd1"/></symbol>
    <symbol id="icon-mail" viewBox="0 0 10 10"><rect x="0.5" y="2" width="9" height="6" fill="#1a8fd1"/><path d="M0.5 2 L5 5.6 L9.5 2" fill="none" stroke="#ffffff" stroke-width="0.8"/></symbol>
    <symbol id="icon-globe" viewBox="0 0 10 10"><circle cx="5" cy="5" r="4.5" fill="#1a8fd1"/><path d="M0.5 5 H9.5 M5 0.5 Q2.5 5 5 9.5 M5 0.5 Q7.5 5 5 9.5" fill="none" stroke="#ffffff" stroke-width="0.6"/></symbol>
  </defs>
</svg>

<section class="card card--grey card--front-grey front">
  <div class="brand-name">Valmira</div>
  <div class="brand-tagline">Integrative Holistic Medicine</div>
  <div class="contact">
    <div class="contact__address">4100 East Marrow Drive<br>Austin, TX 78119</div>
    <div class="contact__row"><svg class="contact__icon"><use href="#icon-phone"/></svg>512 555 0148</div>
    <div class="contact__row"><svg class="contact__icon"><use href="#icon-mobile"/></svg>818 555 0192</div>
    <div class="contact__row"><svg class="contact__icon"><use href="#icon-mail"/></svg>t.wrenfeld@ValmiraHealth.example</div>
    <div class="contact__row"><svg class="contact__icon"><use href="#icon-globe"/></svg>www.ValmiraHealth.example</div>
  </div>
  <div class="practitioner">
    <div class="practitioner__name">Tobias Wrenfeld</div>
    <div class="practitioner__credentials">DOE, CPT, LMT</div>
  </div>
</section>

<section class="card card--white card--front-white front">
  <div class="brand-name">Valmira</div>
  <div class="brand-tagline">Integrative Holistic Medicine</div>
  <div class="contact">
    <div class="contact__address">4100 East Marrow Drive<br>Austin, TX 78119</div>
    <div class="contact__row"><svg class="contact__icon"><use href="#icon-phone"/></svg>512 555 0148</div>
    <div class="contact__row"><svg class="contact__icon"><use href="#icon-mobile"/></svg>818 555 0192</div>
    <div class="contact__row"><svg class="contact__icon"><use href="#icon-mail"/></svg>t.wrenfeld@ValmiraHealth.example</div>
    <div class="contact__row"><svg class="contact__icon"><use href="#icon-globe"/></svg>www.ValmiraHealth.example</div>
  </div>
  <div class="practitioner">
    <div class="practitioner__name">Tobias Wrenfeld</div>
    <div class="practitioner__credentials">DOE, CPT, LMT</div>
  </div>
</section>

<section class="card card--white card--back-white back">
  <div class="brand-name">Valmira</div>
  <div class="brand-tagline">Integrative Holistic Medicine</div>
  <div class="slogan">Helping the body help itself</div>
</section>

<section class="card card--grey card--back-grey back">
  <div class="brand-name">Valmira</div>
  <div class="brand-tagline">Integrative Holistic Medicine</div>
  <div class="slogan">Helping the body help itself</div>
</section>

</body>
</html>
```